Business Card for Multi-Brand Sportswear Company

We are looking for a business card which represents our company and the multiple brands within it.

The company: Fen Athletics (LTD)
The brands: Fen, TavaPuni, ElmStretch, Grit and Rain

Employees using these cards would be representing Fen Athletics, rather than any of the individual brands. You will see a current design within the uploaded files, to give some inspiration. The actual text of the brands is not necessary, but the logos should be on there is some format.

Our creative minds on this are stretched, so we are looking for someone to make this their own, and show us what a good business card should look like.

We may like to get these printed with spot gloss, so keep that in mind with your designs.

www.fenathletics.co.uk

Industry/Entity Type

Business

Contact Information for Business Card

Leo Pemberton-Hale
Operations Manager
(+44) 1632 960 418
Leo@fenathletics.co.uk
www.fenathletics.co.uk

Font styles to use
Sans Serif
Other font styles liked:
• Eurostile

Colors
ffffff

Requirements
Nice to have
• Dark (black) background

```html
<!DOCTYPE html>
<html lang="en">
<head>
<meta charset="utf-8">
<title>Fen Athletics – Business Card</title>
<link rel="stylesheet" href="https://fonts.googleapis.com/css2?family=Saira:wght@400;500;600;700&display=swap">
<style>
  :root {
    --page-bg: #e9e9e9;
    --card-black: #171717;
    --card-brown: #261d15;
    --paper: #ffffff;
    --accent-red: #ff0000;
    --ink-dark: #1d1a17;
    --ink-light: #ffffff;
    --brand-grey: #8c8c8c;
    --brand-red: #e0232b;
    --brand-plum: #6a5468;
  }
  * { margin: 0; padding: 0; box-sizing: border-box; }
  html, body {
    width: 1200px; height: 586px; overflow: hidden;
    background: var(--page-bg);
    font-family: "Saira", sans-serif;
  }
  .sheet { position: relative; width: 1200px; height: 586px; }

  .card {
    position: absolute; top: 129px;
    width: 502px; height: 300px; overflow: hidden;
  }

  /* Front */
  .card-front { left: 65px; background: var(--card-black); }
  .front-wordmark {
    position: absolute; inset: 0;
    display: flex; align-items: center; justify-content: center;
    color: var(--ink-light);
    font-size: 44px; font-weight: 600; letter-spacing: 1px;
  }

  /* Back */
  .card-back { left: 608px; background: var(--card-brown); }
  .back-art { position: absolute; inset: 0; }
  .contact-name {
    position: absolute; left: 26px; top: 42px;
    color: var(--ink-light); font-size: 18px; font-weight: 700;
  }
  .contact-role {
    position: absolute; left: 26px; top: 66px;
    color: var(--ink-light); font-size: 11.5px; font-weight: 400;
  }
  .contact-address {
    position: absolute; left: 26px; top: 129px;
    color: var(--ink-light); font-size: 13px; font-weight: 600; line-height: 17px;
  }
  .contact-lines {
    position: absolute; left: 26px; top: 205px; list-style: none;
    color: var(--ink-light); font-size: 11.5px;
  }
  .contact-lines li { display: flex; align-items: center; height: 24.5px; }
  .contact-lines svg { width: 14px; height: 12px; margin-right: 7px; fill: var(--ink-light); }

  .back-wordmark {
    position: absolute; left: 242px; top: 136px; width: 236px;
    text-align: center; color: var(--ink-dark);
    font-size: 24px; font-weight: 600;
  }
  .brand-row {
    position: absolute; left: 262px; top: 216px; width: 222px;
    display: flex; justify-content: space-between; align-items: center;
    font-size: 11px; font-weight: 600;
  }
  .brand-tavapuni { color: var(--brand-grey); }
  .brand-grit { color: var(--brand-red); }
  .brand-elm { color: var(--brand-plum); }
  .brand-fen { color: var(--ink-dark); }
</style>
</head>
<body>
<main class="sheet">

  <section class="card card-front" aria-label="Card front">
    <div class="front-wordmark">Fen Athletics</div>
  </section>

  <section class="card card-back" aria-label="Card back">
    <svg class="back-art" viewBox="0 0 502 300" aria-hidden="true">
      <path d="M340 0 Q170 150 280 300 L502 300 L502 0 Z" fill="var(--paper)"/>
      <path d="M330 0 C270 35 222 110 220 165 C220 215 245 265 282 300 C258 250 248 205 254 160 C262 95 305 35 360 0 Z" fill="var(--accent-red)"/>
    </svg>

    <h1 class="contact-name">Owen Hartley</h1>
    <p class="contact-role">Managing Director</p>
    <p class="contact-address">Hollin Yard, Marston,<br>Kelby, KE4 2PN</p>

    <ul class="contact-lines">
      <li>
        <svg viewBox="0 0 14 12"><path d="M1 4 Q7 -1 13 4 L11 5.5 L9.5 3.8 L4.5 3.8 L3 5.5 Z M3 6 H11 L12 11 H2 Z"/></svg>
        +44 (0)1632 960418
      </li>
      <li>
        <svg viewBox="0 0 14 12"><path d="M4 0 H10 V3 H4 Z M1 4 H13 V9 H11 V7 H3 V9 H1 Z M4 8 H10 V12 H4 Z"/></svg>
        (555) 014-2290
      </li>
      <li>
        <svg viewBox="0 0 14 12"><path d="M0 1 H14 V11 H0 Z M1.5 2.5 V9.5 L5 6 Z M12.5 2.5 V9.5 L9 6 Z M1.8 2 L7 6.8 L12.2 2 Z M2 10 L5.7 6.6 L7 7.8 L8.3 6.6 L12 10 Z" fill-rule="evenodd"/></svg>
        owen@fenathletics.co.uk
      </li>
    </ul>

    <div class="back-wordmark">Fen Athletics</div>

    <div class="brand-row">
      <span class="brand-tavapuni">TavaPuni</span>
      <span class="brand-grit">Grit and Rain</span>
      <span class="brand-elm">ElmStretch</span>
      <span class="brand-fen">Fen</span>
    </div>
  </section>

</main>
</body>
</html>
```